Accounting firm needing business card / letterhead designed
Marcus L. Trenholm, CPA
marcus@veltrowledger.com
www.veltrowledger.com
842 E Alder Ave Perrysburg, OH 43827
419-562-0974

```html
<!DOCTYPE html>
<html lang="en">
<head>
<meta charset="utf-8">
<title>Veltrow Ledger — Stationery</title>
<link href="https://fonts.googleapis.com/css2?family=Roboto:wght@400;500;700&display=swap" rel="stylesheet">
<style>
  :root {
    --navy: #25215e;
    --green: #7dc242;
    --ink: #6a6a6a;
    --paper: #ffffff;
    --backdrop: #e6e6ea;
  }
  * { margin: 0; padding: 0; box-sizing: border-box; }
  html, body { width: 1200px; height: 984px; overflow: hidden; }
  body {
    background: var(--backdrop);
    font-family: "Roboto", Arial, sans-serif;
    position: relative;
  }

  .brand-name {
    font-family: "Roboto", Arial, sans-serif;
    font-weight: 700;
    letter-spacing: 0.04em;
    text-transform: uppercase;
    white-space: nowrap;
    line-height: 1;
  }

  /* Letterhead */
  .letterhead {
    position: absolute; left: 97px; top: 107px;
    width: 554px; height: 777px;
    background: var(--paper);
    box-shadow: 0 4px 14px rgba(0,0,0,.18);
  }
  .letterhead .brand-name {
    position: absolute; left: 48px; top: 80px;
    font-size: 22px; color: var(--navy);
  }
  .contact-list { list-style: none; color: var(--ink); }
  .letterhead .contact-list {
    position: absolute; left: 396px; top: 46px;
    font-size: 9px; line-height: 13px;
  }
  .contact-list li { display: flex; align-items: center; gap: 5px; }
  .contact-list .address { display: block; margin-bottom: 4px; }
  .contact-list svg { width: 8px; height: 8px; flex: none; }
  .recipient {
    position: absolute; left: 47px; top: 226px;
    font-size: 10px; line-height: 14.5px; color: var(--ink);
  }
  .letter-body {
    position: absolute; left: 47px; top: 314px; width: 461px;
    font-size: 9.8px; line-height: 14.5px; color: var(--ink);
    text-align: justify;
  }
  .letter-body p + p { margin-top: 14.5px; }
  .signature {
    position: absolute; left: 47px; top: 520px;
    width: 105px; height: 68px;
    background: linear-gradient(135deg, rgba(37,33,94,.18), rgba(37,33,94,.06));
  }
  .signer-title {
    position: absolute; left: 46px; top: 603px;
    font-size: 10px; color: var(--ink);
  }
  .footer-rule {
    position: absolute; left: 0; right: 0; top: 752px; height: 3px;
    background: var(--green);
  }
  .footer-band {
    position: absolute; left: 0; right: 0; top: 757px; bottom: 0;
    background: var(--navy);
  }

  /* Business cards */
  .card {
    position: absolute; left: 710px; width: 379px; height: 216px;
    box-shadow: 0 4px 12px rgba(0,0,0,.2);
    overflow: hidden;
  }
  .card-front { top: 251px; background: var(--navy); }
  .card-front .brand-panel {
    position: absolute; left: 0; top: 0; width: 186px; height: 100%;
    background: var(--paper);
    display: flex; align-items: center; justify-content: center;
  }
  .card-front .brand-name { font-size: 14px; color: var(--navy); }
  .card-front .accent-stripe {
    position: absolute; left: 186px; top: 0; width: 4px; height: 100%;
    background: var(--green);
  }
  .card-details { position: absolute; left: 216px; top: 58px; color: #fff; }
  .person-name { font-size: 17px; font-weight: 700; color: var(--green); line-height: 1.1; }
  .person-role { font-size: 12px; margin-top: 3px; }
  .card-details .contact-list {
    color: #fff; font-size: 8.6px; line-height: 13px; margin-top: 12px;
  }
  .card-details .contact-list .address { margin-bottom: 8px; }

  .card-back {
    top: 510px; background: var(--navy);
    display: flex; flex-direction: column; align-items: center;
  }
  .card-back .brand-name {
    margin-top: 96px; font-size: 22px; color: #fff;
  }
  .card-back .site { margin-top: 64px; font-size: 9.5px; color: #fff; }
</style>
</head>
<body>

<svg width="0" height="0" style="position:absolute" aria-hidden="true">
  <defs>
    <symbol id="icon-phone" viewBox="0 0 10 10"><path d="M2.2 0.6 3.6 2.4 2.8 3.4C3.4 4.8 5.2 6.6 6.6 7.2L7.6 6.4 9.4 7.8 8.6 9.4C4.6 9.4 0.6 5.4 0.6 1.4Z" fill="currentColor"/></symbol>
    <symbol id="icon-mail" viewBox="0 0 10 10"><rect x="0.5" y="2" width="9" height="6.2" fill="currentColor"/><path d="M0.8 2.4 5 5.6 9.2 2.4" stroke="#fff" stroke-width="0.8" fill="none"/></symbol>
    <symbol id="icon-web" viewBox="0 0 10 10"><circle cx="5" cy="5" r="4.3" fill="none" stroke="currentColor" stroke-width="1"/><ellipse cx="5" cy="5" rx="1.8" ry="4.3" fill="none" stroke="currentColor" stroke-width="0.8"/><path d="M0.8 5H9.2" stroke="currentColor" stroke-width="0.8"/></symbol>
  </defs>
</svg>

<article class="letterhead">
  <div class="brand-name">Veltrow Ledger</div>
  <ul class="contact-list">
    <li class="address">842 E Alder Ave Perrysburg<br>OH 43827</li>
    <li><svg style="color:var(--navy)"><use href="#icon-phone"/></svg>419-562-0974</li>
    <li><svg style="color:var(--navy)"><use href="#icon-mail"/></svg>marcus@veltrowledger.com</li>
    <li><svg style="color:var(--navy)"><use href="#icon-web"/></svg>www.veltrowledger.com</li>
  </ul>

  <div class="recipient">
    Dear Halvorsen<br>
    Brightmoor Print Works Corporation<br>
    Department Design
  </div>

  <div class="letter-body">
    <p>Lorem ipsum dolor sit amet, consectetuer adipiscing elit. Aenean commodo ligula eget dolor. Aenean massa. Cum sociis natoque penatibus et magnis dis parturient montes, nascetur ridiculus mus. Donec quam felis, ultricies nec, pellentesque eu, pretium quis, sem. Nulla consequat massa quis enim. Donec pede justo, fringilla vel, aliquet nec, vulputate eget, arcu. In enim justo, rhoncus ut, imperdiet a, venenatis vitae, justo. Nullam dictum felis eu pede mollis pretium. Integer tincidunt. Cras dapibus. Vivamus elementum semper nisi.Nullam dictum felis eu pede mollis pretium. Integer tincidunt. Cras dapibus. Vivamus elementum semper nisi.felis eu pede mollis pretium. Integer tincidunt. Cras dapibus.</p>
    <p>Quisque rutrum. Aenean imperdiet. Etiam ultricies nisi vel augue. Curabitur ullamcorper ultricies nisi. Nam eget dui. Etiam rhoncus. Maecenas tempus, tellus eget condimentum rhoncus, sem quam semper libero, sit amet adipiscing sem neque sed ipsum.felis pede mollis pretium. I am tincidunt. Cras dapibus.</p>
  </div>

  <div class="signature" role="img" aria-label="Handwritten signature of the director"></div>
  <div class="signer-title">Director/Excecutive Director</div>

  <div class="footer-rule"></div>
  <div class="footer-band"></div>
</article>

<section class="card card-front">
  <div class="brand-panel"><div class="brand-name">Veltrow Ledger</div></div>
  <div class="accent-stripe"></div>
  <div class="card-details">
    <div class="person-name">Marcus L. Trenholm</div>
    <div class="person-role">CPA</div>
    <ul class="contact-list">
      <li class="address">842 E Alder Ave Perrysburg<br>OH 43827</li>
      <li><svg style="color:var(--green)"><use href="#icon-phone"/></svg>419-562-0974</li>
      <li><svg style="color:var(--green)"><use href="#icon-mail"/></svg>marcus@veltrowledger.com</li>
      <li><svg style="color:var(--green)"><use href="#icon-web"/></svg>www.veltrowledger.com</li>
    </ul>
  </div>
</section>

<section class="card card-back">
  <div class="brand-name">Veltrow Ledger</div>
  <div class="site">www.veltrowledger.com</div>
</section>

</body>
</html>
```